Veltrano.co - Polar Expeditions Specialists

We need a modern, visually striking business card for Veltrano.co, a company specialized in selling expedition cruises to the most remote regions on Earth, with a focus on the Arctic and Antarctica. The design should instantly communicate that the cardholder is an expert in polar travel. Use clean, premium aesthetics with cool tones like icy blue and white, possibly incorporating polar imagery (ice, glaciers, penguins, etc.)

Attached the logo

Contact Information for Business Card

Feels high-end and trustworthy.. Visually memorable — encourages people to keep it

Colors
0054AA
0677BA
7BADD7
CADEEF
E8F1F8

Requirements
Must have
• ice, glaciers, penguins, montains
Nice to have
• modern, transparente,

```html
<!DOCTYPE html>
<html lang="en">
<head>
<meta charset="utf-8">
<title>Veltrano.co – Business Card</title>
<link href="https://fonts.googleapis.com/css2?family=Poppins:wght@400;600;700&display=swap" rel="stylesheet">
<style>
  :root{
    --page:#2b2b2b;
    --blue-deep:#0054AA;
    --blue-card:#3577BA;
    --blue-mid:#0677BA;
    --blue-light:#7BADD7;
    --ice:#CADEEF;
    --frost:#E8F1F8;
    --white:#ffffff;
  }
  *{box-sizing:border-box;margin:0;padding:0}
  html,body{width:1200px;height:1015px;overflow:hidden;background:var(--page);font-family:'Poppins',sans-serif}
  .sheet{position:relative;width:1200px;height:1015px;display:flex;flex-direction:column;align-items:center;justify-content:center;gap:60px}
  .card{position:relative;width:700px;height:400px;overflow:hidden;border-radius:4px;box-shadow:0 14px 30px rgba(0,0,0,.45)}

  /* front */
  .card--front{background:var(--blue-card)}
  .front__scene{position:absolute;inset:0;background:
      radial-gradient(ellipse at 30% 70%, rgba(202,222,239,.35), transparent 55%),
      linear-gradient(180deg,#4f8fcb 0%,#4a88c6 55%,#3f7fc0 100%)}
  .front__brand{position:absolute;inset:0;display:flex;flex-direction:column;align-items:center;justify-content:center;color:var(--white)}
  .brand__row{display:flex;align-items:center;gap:12px}
  .brand__dot{width:22px;height:22px;border-radius:50%;background:var(--white);flex:none}
  .brand__name{font-weight:700;font-size:72px;letter-spacing:.5px;line-height:1;white-space:nowrap}
  .brand__tag{font-weight:600;font-size:20px;margin-top:10px;letter-spacing:.3px;white-space:nowrap}

  /* back */
  .card--back{background:var(--blue-card);color:var(--white)}
  .back__shape{position:absolute;inset:0;width:700px;height:400px}
  .back__info{position:absolute;left:56px;top:66px;width:230px}
  .person__name{font-weight:600;font-size:22px;letter-spacing:.4px;white-space:nowrap;line-height:1.2}
  .person__role{font-size:16px;white-space:nowrap}
  .address{margin-top:64px;font-size:15px;line-height:1.4;white-space:nowrap}
  .contacts{list-style:none;margin-top:20px;font-size:15px;line-height:1.55}
  .contacts li{display:flex;align-items:center;gap:10px;white-space:nowrap}
  .contacts svg{width:17px;height:17px;flex:none}
  .back__brand{position:absolute;left:548px;top:182px;transform:translate(-50%,-50%);display:flex;flex-direction:column;align-items:center;color:var(--blue-card)}
  .back__brand .brand__name{font-size:42px}
  .back__brand .brand__dot{width:15px;height:15px;background:var(--blue-card)}
  .back__brand .brand__tag{font-size:12px;margin-top:8px}
</style>
</head>
<body>
<main class="sheet">
  <section class="card card--front">
    <div class="front__scene" role="img" aria-label="Faint photograph of an icy glacier and floating icebergs washed in blue"></div>
    <div class="front__brand">
      <div class="brand__row"><span class="brand__dot"></span><span class="brand__name">Veltrano.co</span></div>
      <div class="brand__tag">Polar Expeditions Specialists</div>
    </div>
  </section>

  <section class="card card--back">
    <svg class="back__shape" viewBox="0 0 700 400">
      <circle cx="547" cy="96" r="262" fill="var(--white)"/>
      <circle cx="547" cy="96" r="256" fill="var(--blue-card)"/>
      <circle cx="556" cy="92" r="248" fill="var(--white)"/>
    </svg>
    <div class="back__info">
      <div class="person__name">MARCUS HALLOWAY</div>
      <div class="person__role">Managing Director</div>
      <p class="address">18 Harbour Quay Road<br>Northgate, 30917</p>
      <ul class="contacts">
        <li><svg viewBox="0 0 24 24" fill="none" stroke="currentColor" stroke-width="2"><path d="M5 3h4l2 5-3 2a11 11 0 0 0 6 6l2-3 5 2v4a2 2 0 0 1-2 2A17 17 0 0 1 3 5a2 2 0 0 1 2-2z"/></svg>041-555 208 314</li>
        <li><svg viewBox="0 0 24 24" fill="none" stroke="currentColor" stroke-width="2"><rect x="2" y="5" width="20" height="14"/><path d="M2 5l10 8 10-8"/></svg>hello@veltrano.co</li>
        <li><svg viewBox="0 0 24 24" fill="none" stroke="currentColor" stroke-width="2"><circle cx="12" cy="12" r="10"/><path d="M2 12h20M12 2c3 3 3 17 0 20M12 2c-3 3-3 17 0 20"/></svg>www.veltrano.co</li>
      </ul>
    </div>
    <div class="back__brand">
      <div class="brand__row"><span class="brand__dot"></span><span class="brand__name">Veltrano.co</span></div>
      <div class="brand__tag">Polar Expeditions Specialists</div>
    </div>
  </section>
</main>
</body>
</html>
```